Brenvik Systems PowerPoint Template

Project Title: Professional & Functional PowerPoint Template (.potx) – Brenvik Systems Rebrand

Project Overview:
Brenvik Systems has recently undergone a complete rebranding, including a new logo, website, and visual identity. We need a professional, high-end PowerPoint Template (.potx) that reflects our new look while being highly functional for everyday use.

We previously had a design created, but it was built incorrectly (static images, oversized file, no Master Slides). The goal of this project is to take our new aesthetic and build a "workable" template where layouts are controlled by Master Slides and text is easily editable.

Style & Brand Direction:
The template must be an extension of our new website: https://www.brenvik-systems.example/

Aesthetic: Modern, clean, high-tech, and "Industrial Tech."

Color Palette: Please pull the primary blues, greys, and accent colors directly from the website.

Imagery/Graphics: Use clean lines and subtle tech-inspired gradients. Avoid "clutter."

Tone: Innovative, precise, and professional.

Technical Requirements (Crucial)
Format: Must be delivered as a PowerPoint Template file (** .potx **).

Functionality: All layouts must be built using Slide Masters. Users should be able to click "New Slide" and choose from specific layouts.

Native Elements: Do NOT use full-page background images for text areas. Bullet points must use native PowerPoint list functionality (not individual text boxes).

File Size: The template must be optimized and lightweight.

Fonts: Use standard professional fonts or provide the specific web-safe equivalent used on our site (e.g., Montserrat, Open Sans, etc.).

Required Slide Layouts
Please include a minimum of 10–12 Master layouts, including:
*Title Slide (2-3 variations: Dark and Light)
*Agenda/Table of Contents
*Section Header/Divider Slides
*Standard Text/Bullet Slide
*Two-Column Text Slide
*Image + Text Layouts (Left/Right variations)
*Data/Chart Slide (Styled bar/pie charts that match the brand)
*Process/Timeline Slide (Infographic style)
*Section slide

Attachments Provided
Brand Assets (.zip): Contains our new logo in various formats.

Inspiration/Existing PPT: We have attached the previous design created by our web agency. Note: Use this for visual inspiration ONLY. Do not copy the file structure, as it is technically flawed.

Deliverables
Final .potx file.

All used icons or custom graphics in vector format (if applicable).

Instruction note on any specific fonts used.

Target Market(s)

Internal communication and external (investors, customers)

Industry/Entity Type

Semiconductor, Automotive

Requirements
Must have
• A potx file

```html
<!DOCTYPE html>
<html lang="en">
<head>
<meta charset="utf-8">
<title>Brenvik Systems – Presentation Template</title>
<link rel="stylesheet" href="https://fonts.googleapis.com/css2?family=Montserrat:wght@700;800;900&family=Inter:wght@400;500;600;700&display=swap">
<style>
  :root {
    --canvas: #282828;
    --brand-blue: #1f3cf5;
    --sky-blue: #1b8fe0;
    --deep-navy: #0a1a4a;
    --ink: #111111;
    --body-text: #4a4a4a;
    --muted: #6b6b6b;
    --pill-fill: #e8f6fd;
    --pill-edge: #cfe7f6;
    --row-alt: #f3f7fd;
    --track: #eef1f6;
    --white: #ffffff;
  }
  * { box-sizing: border-box; margin: 0; padding: 0; }
  html, body { width: 803px; height: 1200px; overflow: hidden; }
  body { background: var(--canvas); font-family: "Inter", Arial, sans-serif; position: relative; }

  .slide {
    position: absolute; width: 697px; height: 392px; overflow: hidden;
    background: var(--white); transform: scale(0.5123); transform-origin: 0 0;
  }
  .slide-title {
    position: absolute; left: 37px; top: 10px;
    font-family: "Montserrat", Arial, sans-serif; font-weight: 800; font-size: 26px;
    color: var(--brand-blue); letter-spacing: 0.2px;
  }
  .title-rule { position: absolute; left: 0; top: 44px; width: 170px; height: 8px; }
  .wordmark {
    position: absolute; right: 36px; top: 16px; display: flex; align-items: center; gap: 7px;
    font-family: "Montserrat", Arial, sans-serif; font-weight: 800; font-size: 24px; color: var(--ink);
  }
  .wordmark .mark { width: 20px; height: 20px; background: var(--brand-blue); }
  .wave { position: absolute; left: 0; bottom: 0; width: 697px; height: 62px; }
  .page-no {
    position: absolute; left: 326px; top: 362px; width: 44px; height: 44px; border-radius: 50%;
    background: var(--brand-blue); color: var(--white); text-align: center;
    font-family: "Montserrat", Arial, sans-serif; font-weight: 800; font-size: 14px; line-height: 34px;
  }

  /* Cover */
  .cover .cover-photo { position: absolute; inset: 0;
    background: radial-gradient(circle at 62% 70%, #f2c46e 0, #6b83c8 10%, transparent 26%),
                linear-gradient(120deg, #050d2a 0%, #0b2a78 45%, #1e63c4 75%, #0c2f7a 100%); }
  .cover .wordmark { left: 52px; right: auto; top: 48px; font-size: 34px; color: var(--white); gap: 10px; }
  .cover .wordmark .mark { width: 26px; height: 26px; background: var(--white); }
  .cover-headline {
    position: absolute; left: 52px; top: 146px;
    font-family: "Montserrat", Arial, sans-serif; font-weight: 900; font-size: 44px; line-height: 50px;
    color: var(--white); text-transform: uppercase;
  }

  /* Contents */
  .toc-item {
    position: absolute; left: 141px; width: 414px; height: 40px; border-radius: 20px;
    background: linear-gradient(90deg, #e3f4fd, #f5fbff); border: 1px solid var(--pill-edge);
    font-size: 11px; color: #2d2d2d; line-height: 38px; padding-left: 20px;
  }
  .toc-item .num {
    position: absolute; right: 9px; top: 9px; width: 21px; height: 21px; border-radius: 50%;
    background: var(--sky-blue); color: var(--white); font-size: 8px; font-weight: 600;
    text-align: center; line-height: 21px;
  }

  /* Capabilities */
  .capability-photo { position: absolute; left: 122px; top: 125px; width: 196px; height: 196px; border-radius: 50%;
    background: radial-gradient(circle at 50% 45%, #f4f4f4 0, #dcdcdc 55%, #c9c9c9 100%); }
  .connectors { position: absolute; left: 0; top: 0; width: 697px; height: 392px; }
  .capability-card {
    position: absolute; left: 378px; width: 226px; height: 56px; border-radius: 28px;
    background: var(--white); box-shadow: 0 3px 10px rgba(20, 60, 160, 0.14);
    padding: 11px 14px 0 58px;
  }
  .capability-card.is-active { background: linear-gradient(90deg, #1e2f9e, var(--sky-blue)); }
  .capability-card .icon { position: absolute; left: 12px; top: 10px; width: 36px; height: 36px; border-radius: 50%;
    background: linear-gradient(135deg, #1e3aa8, #2b7fd9); border: 3px solid #e6eefc; }
  .capability-card h3 { font-size: 6.5px; font-weight: 700; color: #1e2f9e; margin-bottom: 3px; }
  .capability-card p { font-size: 6px; color: var(--muted); line-height: 1.45; }
  .capability-card.is-active h3, .capability-card.is-active p { color: var(--white); }

  /* Who we are */
  .about-copy { position: absolute; left: 36px; top: 70px; width: 298px; font-size: 10.5px; line-height: 19.2px; color: var(--body-text); text-align: justify; }
  .about-copy p + p { margin-top: 19px; }
  .about-lead { position: absolute; left: 371px; top: 70px; width: 298px; font-size: 11px; line-height: 21px; font-weight: 600; color: var(--ink); }
  .about-list { position: absolute; left: 392px; top: 145px; list-style: none; }
  .about-list li { position: relative; padding-left: 21px; font-size: 10.5px; line-height: 24px; color: #333; }
  .about-list li::before { content: ""; position: absolute; left: 0; top: 8px; width: 8px; height: 8px; border-radius: 50%; background: var(--brand-blue); }

  /* Features table */
  .feature-table { position: absolute; left: 76px; top: 78px; width: 545px; border-collapse: collapse;
    border-radius: 10px; overflow: hidden; box-shadow: 0 4px 14px rgba(20, 60, 160, 0.12); }
  .feature-table th { height: 38px; color: var(--white); font-size: 11px; font-weight: 700; text-align: left; padding-left: 27px; }
  .feature-table th:first-child { background: var(--sky-blue); width: 196px; }
  .feature-table th:last-child { background: var(--brand-blue); border-left: 2px solid #fff; }
  .feature-table td { height: 52px; vertical-align: middle; padding: 0 27px; }
  .feature-table td:first-child { font-size: 7.5px; font-weight: 700; color: var(--brand-blue); border-right: 2px solid #fff; }
  .feature-table td:last-child { font-size: 7.8px; color: var(--muted); line-height: 16px; padding-left: 32px; }
  .feature-table tr:nth-child(odd) td { background: var(--row-alt); }
  .feature-table tbody tr:nth-child(even) td { background: var(--white); }

  /* Solutions */
  .solutions-head { position: absolute; left: 0; top: 74px; width: 697px; text-align: center;
    font-size: 12.5px; font-weight: 700; line-height: 19px; color: var(--ink); }
  .solutions-intro { position: absolute; left: 108px; top: 120px; width: 481px; text-align: center;
    font-size: 8.8px; line-height: 17px; color: var(--muted); }
  .solution { position: absolute; top: 186px; width: 150px; text-align: center; }
  .solution .badge { width: 64px; height: 64px; margin: 0 auto; border-radius: 50%;
    background: linear-gradient(135deg, #2a5bf0, var(--sky-blue)); box-shadow: 0 4px 10px rgba(30, 80, 220, 0.3);
    display: flex; align-items: center; justify-content: center; }
  .solution h3 { margin-top: 15px; font-size: 9px; font-weight: 700; color: var(--brand-blue); }
  .solution p { margin-top: 4px; font-size: 8.5px; line-height: 16.5px; color: var(--muted); }

  /* Approach */
  .approach-copy { position: absolute; left: 44px; top: 82px; width: 296px; font-size: 8.8px; line-height: 19px; color: var(--body-text); text-align: justify; }
  .approach-copy .lead { color: var(--ink); font-weight: 600; line-height: 17px; margin-bottom: 9px; }
  .approach-copy p + p { margin-top: 17px; }
  .bar-row { position: absolute; left: 373px; width: 280px; height: 22px; border-radius: 11px; background: var(--track); }
  .bar-row .fill { height: 22px; border-radius: 11px; background: var(--brand-blue); }
  .bar-row.is-sky .fill { background: var(--sky-blue); }
  .bar-row .value { position: absolute; right: 10px; top: 0; font-size: 6px; color: var(--muted); line-height: 22px; }

  /* Collaboration */
  .collab-intro { position: absolute; left: 130px; top: 70px; width: 437px; text-align: center; font-size: 10.5px; line-height: 17px; color: var(--body-text); }
  .timeline { position: absolute; left: 0; top: 0; width: 697px; height: 392px; }
  .stage-pill { position: absolute; width: 126px; height: 26px; border-radius: 13px;
    background: linear-gradient(90deg, var(--brand-blue), #2a6bf2); box-shadow: 0 3px 8px rgba(30, 60, 220, 0.3);
    color: var(--white); font-size: 7.5px; font-weight: 700; text-align: center; line-height: 26px; }
  .stage-note { position: absolute; width: 150px; text-align: center; font-size: 8.2px; line-height: 14px; color: var(--muted); }

  /* Closing */
  .closing { background: linear-gradient(120deg, #1d35e8 0%, #1f4fe6 50%, #1a7fd8 100%); }
  .closing h2 { position: absolute; left: 406px; top: 50px; font-family: "Montserrat", Arial, sans-serif; font-weight: 900; font-size: 34px; color: var(--white); }
  .closing .tagline { position: absolute; left: 406px; top: 98px; width: 248px; font-size: 11.5px; line-height: 20px; color: var(--white); text-align: justify; }
  .contact-list { position: absolute; left: 420px; top: 168px; list-style: none; }
  .contact-list li { position: relative; padding-left: 27px; font-size: 11.5px; line-height: 26px; color: var(--white); width: 230px; }
  .contact-list svg { position: absolute; left: 0; top: 7px; }
  .site-button { position: absolute; left: 406px; top: 290px; width: 245px; height: 38px; border-radius: 19px; background: var(--white);
    color: var(--brand-blue); font-size: 10px; font-weight: 700; line-height: 38px; padding-left: 54px; }
  .site-button::before { content: ""; position: absolute; left: 34px; top: 15px; width: 9px; height: 9px; border-radius: 50%; background: var(--brand-blue); }
</style>
</head>
<body>

<svg width="0" height="0" style="position:absolute" aria-hidden="true">
  <defs>
    <linearGradient id="waveGrad" x1="0" x2="1" y1="0" y2="0">
      <stop offset="0" stop-color="#1b8fe0"/>
      <stop offset="1" stop-color="#1f3cf5"/>
    </linearGradient>
  </defs>
</svg>

<!-- Cover -->
<section class="slide cover" style="left:223px; top:47px;">
  <div class="cover-photo" role="img" aria-label="Photo of an industrial laser cutting head firing sparks onto a metal sheet in blue light"></div>
  <div class="wordmark"><span class="mark"></span>BRENVIK</div>
  <h1 class="cover-headline">Build<br>Tomorrow<br>With Today's<br>Light</h1>
</section>

<!-- Table of contents -->
<section class="slide" style="left:30px; top:273px;">
  <h2 class="slide-title">TABLE OF CONTENTS</h2>
  <svg class="title-rule" viewBox="0 0 170 8"><line x1="0" y1="4" x2="164" y2="4" stroke="#1b8fe0" stroke-width="1.5"/><circle cx="164" cy="4" r="3.5" fill="#1b8fe0"/></svg>
  <div class="wordmark"><span class="mark"></span>BRENVIK</div>
  <div class="toc-item" style="top:75px;">Welcome to Brenvik Systems<span class="num">01</span></div>
  <div class="toc-item" style="top:127px;">Who We Are ( About Brenvik Systems)<span class="num">02</span></div>
  <div class="toc-item" style="top:180px;">Partner With Precision<span class="num">03</span></div>
  <div class="toc-item" style="top:232px;">Laser Wafering Services<span class="num">04</span></div>
  <div class="toc-item" style="top:285px;">Thank You<span class="num">05</span></div>
  <svg class="wave" viewBox="0 0 697 62" preserveAspectRatio="none"><path d="M0 2 Q348 82 697 2 L697 62 L0 62Z" fill="url(#waveGrad)"/></svg>
  <div class="page-no">02</div>
</section>

<!-- Capabilities -->
<section class="slide" style="left:416px; top:271px;">
  <h2 class="slide-title">OUR CAPABILITIES</h2>
  <svg class="title-rule" viewBox="0 0 170 8"><line x1="0" y1="4" x2="164" y2="4" stroke="#1b8fe0" stroke-width="1.5"/><circle cx="164" cy="4" r="3.5" fill="#1b8fe0"/></svg>
  <div class="wordmark"><span class="mark"></span>BRENVIK</div>
  <div class="capability-photo" role="img" aria-label="Product photo of a black laser nozzle emitting a soft beam"></div>
  <svg class="connectors" viewBox="0 0 697 392" aria-hidden="true">
    <path d="M320 223 H338 C350 223 350 150 378 150" fill="none" stroke="#8a98b8" stroke-width="1" stroke-dasharray="2 2"/>
    <path d="M320 223 H378" fill="none" stroke="#8a98b8" stroke-width="1" stroke-dasharray="2 2"/>
    <path d="M320 223 H338 C350 223 350 293 378 293" fill="none" stroke="#8a98b8" stroke-width="1" stroke-dasharray="2 2"/>
  </svg>
  <div class="capability-card" style="top:122px;"><span class="icon"></span><h3>CUSTOM MATERIAL PROCESSING</h3><p>Sed ut perspiciatis unde omnis iste natus error sit voluptatem accusantium</p></div>
  <div class="capability-card is-active" style="top:194px;"><span class="icon"></span><h3>PROTOTYPE DEVELOPMENT &amp; TESTING</h3><p>Sed ut perspiciatis unde omnis iste natus error sit voluptatem accusantium</p></div>
  <div class="capability-card" style="top:265px;"><span class="icon"></span><h3>TECHNICAL SUPPORT &amp; TRAINING</h3><p>Sed ut perspiciatis unde omnis iste natus error sit voluptatem accusantium</p></div>
  <svg class="wave" viewBox="0 0 697 62" preserveAspectRatio="none"><path d="M0 2 Q348 82 697 2 L697 62 L0 62Z" fill="url(#waveGrad)"/></svg>
  <div class="page-no">06</div>
</section>

<!-- Who we are -->
<section class="slide" style="left:30px; top:500px;">
  <h2 class="slide-title">WHO WE ARE</h2>
  <svg class="title-rule" viewBox="0 0 170 8"><line x1="0" y1="4" x2="164" y2="4" stroke="#1b8fe0" stroke-width="1.5"/><circle cx="164" cy="4" r="3.5" fill="#1b8fe0"/></svg>
  <div class="wordmark"><span class="mark"></span>BRENVIK</div>
  <div class="about-copy">
    <p>Founded in 2014, we emerged to replace wasteful mechanical manufacturing with laser precision. Today we deliver 2.2-2.3 wafers per mm with $132M in funding.</p>
    <p>We don't optimize existing processes—we eliminate them. Our breakthrough approach creates manufacturing methods that seemed impossible years ago.</p>
    <p>From California to facilities worldwide, our process reduces costs by more than 60% while cutting waste—making clean technology more accessible and efficient.</p>
  </div>
  <p class="about-lead">Harnessing the power of light to deliver precision, scalability, and sustainability across every stage of production.</p>
  <ul class="about-list">
    <li>Founded in 2024</li>
    <li>2–3x improvement in wafer throughput</li>
    <li>+60% cost savings at scale</li>
    <li>Quis autem vel eum iure reprehenderit qui</li>
    <li>Voluptate velit esse quam nihil molestiae con</li>
    <li>Vel illum qui dolorem eum fugiat</li>
    <li>Quo voluptas nulla pariatur?</li>
  </ul>
  <svg class="wave" viewBox="0 0 697 62" preserveAspectRatio="none"><path d="M0 2 Q348 82 697 2 L697 62 L0 62Z" fill="url(#waveGrad)"/></svg>
  <div class="page-no">03</div>
</section>

<!-- Features -->
<section class="slide" style="left:416px; top:495px;">
  <h2 class="slide-title">OUR FEATURES</h2>
  <svg class="title-rule" viewBox="0 0 170 8"><line x1="0" y1="4" x2="164" y2="4" stroke="#1b8fe0" stroke-width="1.5"/><circle cx="164" cy="4" r="3.5" fill="#1b8fe0"/></svg>
  <div class="wordmark"><span class="mark"></span>BRENVIK</div>
  <table class="feature-table">
    <thead><tr><th>FEATURES</th><th>FIELD SERVICES PARTNER STATUS</th></tr></thead>
    <tbody>
      <tr><td>UT ENIM AD MINIMA</td><td>Ut enim ad minima veniam, quis nostrum exercitationem ullam corporis suscipit laboriosam, nisi ut aliquid ex ea</td></tr>
      <tr><td>QUIS AUTEM VEL EUM IURE REPR</td><td>Ut enim ad minima veniam, quis nostrum exercitationem ullam corporis suscipit laboriosam, nisi ut aliquid ex ea</td></tr>
      <tr><td>EOS QUI RATIONE VOLUPTATEM SE</td><td>Ut enim ad minima veniam, quis nostrum exercitationem ullam corporis suscipit laboriosam, nisi ut aliquid ex ea</td></tr>
      <tr><td>SED UT PERSPICIATIS UNDE OMNIS</td><td>Ut enim ad minima veniam, quis nostrum exercitationem ullam corporis suscipit laboriosam, nisi ut aliquid ex ea</td></tr>
    </tbody>
  </table>
  <svg class="wave" viewBox="0 0 697 62" preserveAspectRatio="none"><path d="M0 2 Q348 82 697 2 L697 62 L0 62Z" fill="url(#waveGrad)"/></svg>
  <div class="page-no">07</div>
</section>

<!-- Solutions -->
<section class="slide" style="left:30px; top:726px;">
  <h2 class="slide-title">OUR SOLUTIONS</h2>
  <svg class="title-rule" viewBox="0 0 170 8"><line x1="0" y1="4" x2="164" y2="4" stroke="#1b8fe0" stroke-width="1.5"/><circle cx="164" cy="4" r="3.5" fill="#1b8fe0"/></svg>
  <div class="wordmark"><span class="mark"></span>BRENVIK</div>
  <p class="solutions-head">HARNESSING THE POWER OF LIGHT TO DELIVER PRECISION,<br>SCALABILITY, &amp; SUSTAINABILITY ACROSS EVERY STAGE OF PRODUCTION.</p>
  <p class="solutions-intro">Sed ut perspiciatis unde omnis iste natus error sit voluptatem accusantium doloremque laudantium, totam rem aperiam, eaque ipsa quae ab illo inventore veritatis et quasi architecto beatae vitae dicta sunt explicabo Nemo enim ipsam voluptatem quia voluptas sit aspernatur aut odit.</p>
  <div class="solution" style="left:104px;">
    <div class="badge"><svg width="26" height="26" viewBox="0 0 26 26"><circle cx="13" cy="13" r="12" fill="#fff"/><path d="M7.5 13.5l3.5 3.5 7-7.5" fill="none" stroke="#1f3cf5" stroke-width="2.6" stroke-linecap="round" stroke-linejoin="round"/></svg></div>
    <h3>SIC WAFERS</h3><p>We deliver 2.2-2.3 wafers per mm with four quality grades aligned to your needs.</p>
  </div>
  <div class="solution" style="left:273px;">
    <div class="badge"><svg width="26" height="26" viewBox="0 0 26 26"><circle cx="13" cy="13" r="12" fill="#fff"/><path d="M7.5 13.5l3.5 3.5 7-7.5" fill="none" stroke="#1f3cf5" stroke-width="2.6" stroke-linecap="round" stroke-linejoin="round"/></svg></div>
    <h3>LASER WAFERING</h3><p>No upfront equipment costs. No capacity risk.</p>
  </div>
  <div class="solution" style="left:442px;">
    <div class="badge"><svg width="26" height="26" viewBox="0 0 26 26"><circle cx="13" cy="13" r="12" fill="#fff"/><path d="M7.5 13.5l3.5 3.5 7-7.5" fill="none" stroke="#1f3cf5" stroke-width="2.6" stroke-linecap="round" stroke-linejoin="round"/></svg></div>
    <h3>CUSTOM SOLUTIONS</h3><p>Every production challenge is unique. Our team works with you to develop custom wafering solutions</p>
  </div>
  <svg class="wave" viewBox="0 0 697 62" preserveAspectRatio="none"><path d="M0 2 Q348 82 697 2 L697 62 L0 62Z" fill="url(#waveGrad)"/></svg>
  <div class="page-no">04</div>
</section>

<!-- Approach -->
<section class="slide" style="left:415px; top:718px;">
  <h2 class="slide-title">OUR APPROACH</h2>
  <svg class="title-rule" viewBox="0 0 170 8"><line x1="0" y1="4" x2="164" y2="4" stroke="#1b8fe0" stroke-width="1.5"/><circle cx="164" cy="4" r="3.5" fill="#1b8fe0"/></svg>
  <div class="wordmark"><span class="mark"></span>BRENVIK</div>
  <div class="approach-copy">
    <p class="lead">Ut enim ad minima veniam, quis nostrum exercitationem ullam corporis suscipit laboriosam, nisi ut aliquid ex ea commodi consequatur? Quis autem vel eum</p>
    <p>Nemo enim ipsam voluptatem quia voluptas sit aspernatur aut odit aut fugit, sed quia consequuntur magni dolores eos qui ratione voluptatem sequi nesciunt. Neque porro quisquam est, qui dolorem ipsum quia dolor sit amet, consectetur, adipisci velit, sed quia non numquam eius modi tempora incidunt ut labore et dolore magnam aliquam quaerat voluptatem.</p>
    <p>Ut enim ad minima veniam, quis nostrum exercitationem ullam corporis suscipit laboriosam, nisi ut aliquid ex ea commodi</p>
  </div>
  <div class="bar-row" style="top:84px;"><div class="fill" style="width:157px;"></div><span class="value">60%</span></div>
  <div class="bar-row is-sky" style="top:118px;"><div class="fill" style="width:197px;"></div><span class="value">80%</span></div>
  <div class="bar-row" style="top:152px;"><div class="fill" style="width:117px;"></div><span class="value">40%</span></div>
  <div class="bar-row is-sky" style="top:185px;"><div class="fill" style="width:92px;"></div><span class="value">30%</span></div>
  <div class="bar-row" style="top:219px;"><div class="fill" style="width:182px;"></div><span class="value">70%</span></div>
  <div class="bar-row is-sky" style="top:253px;"><div class="fill" style="width:153px;"></div><span class="value">60%</span></div>
  <div class="bar-row" style="top:287px;"><div class="fill" style="width:218px;"></div><span class="value">70%</span></div>
  <svg class="wave" viewBox="0 0 697 62" preserveAspectRatio="none"><path d="M0 2 Q348 82 697 2 L697 62 L0 62Z" fill="url(#waveGrad)"/></svg>
  <div class="page-no">08</div>
</section>

<!-- Collaboration -->
<section class="slide" style="left:30px; top:952px;">
  <h2 class="slide-title">COLLABORATION BUILT IN</h2>
  <svg class="title-rule" viewBox="0 0 170 8"><line x1="0" y1="4" x2="164" y2="4" stroke="#1b8fe0" stroke-width="1.5"/><circle cx="164" cy="4" r="3.5" fill="#1b8fe0"/></svg>
  <div class="wordmark"><span class="mark"></span>BRENVIK</div>
  <p class="collab-intro">Our customer relationships start with questions, not quotations. We work together to optimize wafer characteristics for your downstream fabrication, ensuring every specification serves your end goals.</p>
  <svg class="timeline" viewBox="0 0 697 392" aria-hidden="true">
    <line x1="71" y1="232" x2="632" y2="232" stroke="#1b8fe0" stroke-width="2"/>
    <path d="M630 227 L639 232 L630 237Z" fill="#1b8fe0"/>
    <circle cx="122" cy="232" r="4.5" fill="#fff" stroke="#1b8fe0" stroke-width="1.6"/>
    <circle cx="269" cy="232" r="4.5" fill="#fff" stroke="#1b8fe0" stroke-width="1.6"/>
    <circle cx="416" cy="232" r="4.5" fill="#fff" stroke="#1b8fe0" stroke-width="1.6"/>
    <circle cx="564" cy="232" r="4.5" fill="#fff" stroke="#1b8fe0" stroke-width="1.6"/>
  </svg>
  <p class="stage-note" style="left:194px; top:142px;">Co-developing the process recipe for your needs</p>
  <div class="stage-pill" style="left:206px; top:184px;">COLLABORATION</div>
  <p class="stage-note" style="left:489px; top:142px;">Continuous improvement as your needs advance</p>
  <div class="stage-pill" style="left:501px; top:184px;">EVOLUTION</div>
  <div class="stage-pill" style="left:59px; top:258px;">DISCOVERY</div>
  <p class="stage-note" style="left:47px; top:296px;">Understanding your unique requirements</p>
  <div class="stage-pill" style="left:353px; top:258px;">DELIVERY</div>
  <p class="stage-note" style="left:341px; top:296px;">Consistent quality at production scale</p>
  <svg class="wave" viewBox="0 0 697 62" preserveAspectRatio="none"><path d="M0 2 Q348 82 697 2 L697 62 L0 62Z" fill="url(#waveGrad)"/></svg>
  <div class="page-no">05</div>
</section>

<!-- Thank you -->
<section class="slide closing" style="left:415px; top:952px;">
  <h2>THANK YOU</h2>
  <p class="tagline">We're the Northfield spinout turning light into breakthrough precision—building the backbone of an electrified future.</p>
  <ul class="contact-list">
    <li><svg width="11" height="12" viewBox="0 0 11 12"><path d="M5.5 0C2.7 0 .8 2 .8 4.5 .8 7.8 5.5 12 5.5 12S10.2 7.8 10.2 4.5C10.2 2 8.3 0 5.5 0Zm0 6.3a1.8 1.8 0 1 1 0-3.6 1.8 1.8 0 0 1 0 3.6Z" fill="#fff"/></svg>1480 Orchard Loop, Harlow Vale, CA 95000</li>
    <li><svg width="11" height="12" viewBox="0 0 11 12"><path d="M2.4.6l1.8 2.4-1 1.4c.7 1.6 2 2.9 3.4 3.6l1.4-1 2.4 1.8-.8 2C6.5 11 .5 5 .6 1.4Z" fill="#fff"/></svg>+1 555 010 0188</li>
    <li><svg width="12" height="10" viewBox="0 0 12 10"><rect x="0" y="1" width="12" height="8.5" rx="1" fill="#fff"/><path d="M.5 1.5 6 5.5l5.5-4" fill="none" stroke="#1f4fe6" stroke-width="1.1"/></svg>info@brenvik-systems.example</li>
  </ul>
  <div class="site-button">WWW.BRENVIK-SYSTEMS.EXAMPLE</div>
</section>

</body>
</html>
```